Corvana Tongue Works, LLC

We need a business card that includes information about our business and conveys a reliable business that provides document translation services and interpreters for a variety of corporate and individual clients. We want to come across as professional, reliable, yet approachable. It should include the following on one side:

ESL / ENL Language Classes, Private Lessons, and Online Tutors
PLEXA Training and Testing
Translating & Interpreting Services
Contact us about Over-the-Phone Interpreting in over 200 languages
24/7/365
www.corvanatongue.example

The other side should include (555) 481-3062

Rhoda Pelling, President
482 Garnet Ave., Ste. 219
Indianapolis, IN 40917

Please add USA as part of the address. Also, please add rmpelling@corvanatongueworks.example as the e-mail address. Thank you.

Target Market(s)

Business professionals, their families, the international community

Industry/Entity Type

Business

Contact Information for Business Card

24/7/365
www.corvanatongue.example

(555) 481-3062

Rhoda Pelling, President
482 Garnet Ave., Ste. 219
Indianapolis, IN 40917
USA

Font styles to use
Sans Serif

Colors

Designer to choose colors to be used in the design.

Requirements
Must have
• See project description
• e-mail address and web address
• Phone number
Nice to have
• a globe
• physical address
Should not have
• Should not have the same color scheme as other agencies in our market in Indiana unless it is blue and black. No purple or yellow.

```html
<!DOCTYPE html>
<html lang="en">
<head>
<meta charset="utf-8">
<title>Corvana Tongue Works, LLC – Business Card</title>
<link href="https://fonts.googleapis.com/css2?family=Lato:wght@400;700&display=swap" rel="stylesheet">
<style>
  :root {
    --backdrop: #545454;
    --card-white: #ffffff;
    --brand-blue: #1f8fd3;
    --ink: #111111;
    --rule: #9a9a9a;
    --on-blue: #ffffff;
  }
  * { margin: 0; padding: 0; box-sizing: border-box; }
  html, body { width: 1200px; height: 900px; overflow: hidden; }
  body {
    background: var(--backdrop);
    font-family: "Lato", "Helvetica Neue", Arial, sans-serif;
    position: relative;
  }
  .card {
    position: absolute;
    top: 170px;
    width: 347px;
    height: 561px;
    box-shadow: 3px 4px 6px rgba(0,0,0,0.45);
  }
  .card-front { left: 259px; background: var(--card-white); color: var(--ink); }
  .card-back  { left: 631px; background: var(--brand-blue); color: var(--on-blue); }

  /* Brand lockup */
  .brand {
    position: absolute;
    left: 33px;
    top: 104px;
    display: flex;
    align-items: center;
    gap: 14px;
  }
  .brand-dot {
    width: 120px;
    height: 120px;
    border-radius: 50%;
    background: var(--brand-blue);
    flex: none;
  }
  .brand-name {
    font-weight: 400;
    font-size: 29px;
    line-height: 37px;
    color: var(--ink);
  }

  /* Contact block */
  .contact {
    position: absolute;
    left: 0;
    right: 0;
    top: 340px;
    text-align: center;
  }
  .person-name {
    font-size: 21px;
    font-weight: 700;
    letter-spacing: 0.3px;
    line-height: 26px;
  }
  .person-name .first { color: var(--brand-blue); }
  .person-title { font-size: 15.5px; line-height: 20px; }
  .divider {
    width: 166px;
    height: 1px;
    background: var(--rule);
    margin: 10px auto;
  }
  .address { font-size: 16.5px; line-height: 21px; }
  .phone { font-size: 16.5px; line-height: 21px; }
  .phone .label { color: var(--brand-blue); }
  .email { font-size: 14.5px; line-height: 20px; }
  .web-front { font-size: 16.5px; line-height: 21px; color: var(--brand-blue); }

  /* Back side */
  .services {
    position: absolute;
    left: 0;
    right: 0;
    top: 208px;
    text-align: center;
    font-size: 20px;
    line-height: 24px;
  }
  .services p { margin-bottom: 13px; }
  .availability {
    position: absolute;
    left: 0;
    right: 0;
    top: 459px;
    text-align: center;
    font-size: 23px;
    line-height: 31px;
  }
</style>
</head>
<body>
  <section class="card card-front" aria-label="Card front">
    <div class="brand">
      <div class="brand-dot"></div>
      <div class="brand-name">Corvana<br>Tongue<br>Works, LLC</div>
    </div>
    <div class="contact">
      <div class="person-name"><span class="first">RHODA</span> PELLING</div>
      <div class="person-title">President</div>
      <div class="divider"></div>
      <div class="address">482 Garnet Ave., Ste. 219<br>Indianapolis, IN 40917 USA</div>
      <div class="divider"></div>
      <div class="phone"><span class="label">P:</span> (555) 481-3062</div>
      <div class="email">rmpelling@corvanatongueworks.example</div>
      <div class="web-front">www.corvanatongue.example</div>
    </div>
  </section>

  <section class="card card-back" aria-label="Card back">
    <div class="services">
      <p>ESL / ENL Language Classes,<br>Private Lessons, and Online Tutors</p>
      <p>PLEXA Training and Testing</p>
      <p>Translating &amp; Interpreting Services</p>
      <p>Contact us about Over-the-Phone<br>Interpreting in over 200 languages</p>
    </div>
    <div class="availability">24/7/365<br>www.corvanatongue.example</div>
  </section>
</body>
</html>
```